Quorva - corporate Business Card

We need a good look and innovative business card for a new start up company based in Los Angeles called "Quorva". We are in a payment business, including payment card, app, and ewallet. We are expert in online payment and Card not present (CNP) transaction.
We need an innovative, modern business card.

Our logo font is Aero Matics

Target Market(s)

Startup - Bank - Online Payment - Card Manufacturing

Industry/Entity Type

Startup

Contact Information for Business Card

phone: 555 014 7396 - Address: 4172 Marlowe blvd, Harlan Park, NV 89014

Requirements
Must have
• Message: innovative, professional, expert, high tech, trust, online payment expert, security
Nice to have
• no comment
Should not have
• no Comment

```html
<!DOCTYPE html>
<html lang="en">
<head>
<meta charset="utf-8">
<title>Quorva – Business Card</title>
<link rel="stylesheet" href="https://fonts.googleapis.com/css2?family=Open+Sans:wght@400;600&display=swap">
<style>
  :root {
    --brand-red: #b71f2e;
    --paper: #ffffff;
    --ink: #4d4d4d;
    --rule: #d6d6d6;
    --backdrop: #ecebe8;
  }
  * { margin: 0; padding: 0; box-sizing: border-box; }
  html, body { width: 1200px; height: 987px; overflow: hidden; }
  body {
    position: relative;
    background: var(--backdrop);
    font-family: "Open Sans", Arial, sans-serif;
    color: var(--ink);
  }
  .card {
    position: absolute;
    left: 293px;
    width: 615px;
    box-shadow: 0 3px 10px rgba(0,0,0,0.18);
  }
  .card-front {
    top: 130px;
    height: 351px;
    background: var(--paper);
  }
  .front-edge {
    position: absolute;
    left: 0; right: 0; bottom: 18px;
    height: 5px;
    background: linear-gradient(#bdbdbd, #e6e6e6);
  }
  .front-band {
    position: absolute;
    left: 0; right: 0; bottom: 0;
    height: 18px;
    background: var(--brand-red);
  }
  .brand {
    position: absolute;
    display: flex;
    align-items: center;
    color: var(--brand-red);
    font-weight: 600;
  }
  .brand-dot { border-radius: 50%; background: currentColor; flex: none; }
  .front-brand { left: 62px; top: 142px; font-size: 46px; }
  .front-brand .brand-dot { width: 68px; height: 68px; margin-right: 10px; }
  .divider {
    position: absolute;
    left: 320px; top: 75px;
    width: 1px; height: 194px;
    background: var(--rule);
  }
  .contact {
    position: absolute;
    left: 346px; top: 80px;
    font-size: 16px;
    line-height: 1.4;
  }
  .contact-name {
    color: var(--brand-red);
    font-weight: 600;
    font-size: 20px;
    line-height: 1.2;
  }
  .contact-title { margin-top: 2px; margin-bottom: 11px; }
  .contact-address { margin-bottom: 10px; }
  .contact-line { display: flex; align-items: center; gap: 8px; height: 24px; }
  .contact-line svg { width: 14px; height: 14px; fill: var(--brand-red); flex: none; }

  .card-back {
    top: 506px;
    height: 351px;
    background: var(--brand-red);
    color: var(--paper);
  }
  .back-brand {
    left: 116px; top: 110px;
    color: var(--paper);
    font-size: 76px;
    font-weight: 400;
  }
  .back-brand .brand-dot { width: 110px; height: 110px; margin-right: 16px; }
  .back-url {
    position: absolute;
    left: 0; right: 0; top: 290px;
    text-align: center;
    font-size: 15px;
    letter-spacing: 0.55em;
  }
</style>
</head>
<body>
  <section class="card card-front">
    <div class="brand front-brand"><span class="brand-dot"></span>quorva</div>
    <div class="divider"></div>
    <div class="contact">
      <p class="contact-name">DANA WHITLOCK</p>
      <p class="contact-title">CEO&amp;Founder</p>
      <p class="contact-address">4172 Marlowe blvd<br>Harlan Park, NV 89014</p>
      <p class="contact-line">
        <svg viewBox="0 0 16 16" aria-hidden="true"><path d="M3.6 1.2l2.3 2.6-1.3 1.7c.9 2 2.3 3.5 4.3 4.4l1.7-1.3 2.6 2.3-1.4 2.2C7 12.9 3 8.9 1.6 2.6z"/></svg>
        555 014 7396
      </p>
      <p class="contact-line">
        <svg viewBox="0 0 16 16" aria-hidden="true"><path d="M1 3h14v1.2L8 8.6 1 4.2zM1 5.6l7 4.4 7-4.4V13H1z"/></svg>
        dana@quorva.com
      </p>
      <p class="contact-line">
        <svg viewBox="0 0 16 16" aria-hidden="true"><path d="M8 1a7 7 0 1 0 0 14A7 7 0 0 0 8 1zm-1 2.2c-.4 1 .6 1.6.2 2.6-.5 1-2 .6-2.4 1.8-.3 1 .9 1.6.5 2.8-.2.6-1 .8-1.6.6A5 5 0 0 1 7 3.2zm2.5 9.6c.2-1 1-1.4.9-2.5-.1-1-1.4-1-1.5-2-.1-.9 1-1.2 1.800-1.6.7-.3 1.1-.9 1.6-1.2a5 5 0 0 1-2.8 7.3z"/></svg>
        www.quorva.com
      </p>
    </div>
    <div class="front-edge"></div>
    <div class="front-band"></div>
  </section>

  <section class="card card-back">
    <div class="brand back-brand"><span class="brand-dot"></span>quorva</div>
    <p class="back-url">www.quorva.com</p>
  </section>
</body>
</html>
```